Business Cards

I am a landscape designer and I am hired to do over the top landscapes!
I pay attention to detail and do everything from growing my own orchids and Fruits and Vegetables.
I build ponds water features. I do Landscape Lighting and Specialize in Drip Irrigation for New Landscapes.
I am looking for something with a picture of one of my landscapes and pictures of Orchids on the back so I can work on growing my Orchid business.
I like the plastic cards.
I like Saturation
I like color and I want something that really sticks out!
I will attach a few pics!
Thanks
Corey
A Verdant Terrace LLC
Corey Halvorsen
Orchids & Organic Farming
Landscaping Made Simple
561-555-0147
Averdantterrace@mailbrook.net
West Palm Beach FL

Target Market(s)

I work for Wealthy Clients who want unique designs and enjoy rare plants.
I am the goto guy for tropical and rare plants
Cool Designs
Orchids
Interior Decorating
Exterior Lighting
Organic Farming
People who appreciate plants

Industry/Entity Type

Landscape

Font styles to use
Decorative

Requirements
Must have
• COLOR COLOR COLOR
Saturation
Sleek and Clean
Should not have
• tacky

```html
<!DOCTYPE html>
<html lang="en">
<head>
<meta charset="utf-8">
<title>A Verdant Terrace LLC — Business Cards</title>
<link rel="stylesheet" href="https://fonts.googleapis.com/css2?family=Bebas+Neue&family=Cabin:wght@500&display=swap">
<style>
  :root {
    --backdrop: #e8e2d8;
    --leaf-deep: #0d3d12;
    --leaf-mid: #1f7a22;
    --leaf-bright: #4fb52e;
    --white: #ffffff;
    --phone-yellow: #f5b800;
    --phone-green: #5fd12a;
    --band-black: #0d0606;
    --orchid-magenta: #c41a8e;
    --orchid-yellow: #f2d10c;
    --orchid-violet: #5b1fd6;
    --orchid-orange: #f4642a;
  }
  html, body {
    margin: 0;
    width: 1200px;
    height: 900px;
    overflow: hidden;
    background: var(--backdrop);
  }
  .canvas {
    position: relative;
    width: 1200px;
    height: 900px;
  }
  .card {
    position: absolute;
    width: 644px;
    height: 366px;
    border-radius: 20px;
    overflow: hidden;
    box-shadow: 0 4px 14px rgba(0,0,0,0.25);
  }
  .card--front { left: 278px; top: 50px; }
  .card--back { left: 279px; top: 481px; }

  /* Front */
  .foliage-photo {
    position: absolute;
    inset: 0;
    background:
      radial-gradient(ellipse at 25% 30%, var(--leaf-bright) 0%, transparent 45%),
      radial-gradient(ellipse at 70% 75%, var(--leaf-mid) 0%, transparent 55%),
      linear-gradient(135deg, var(--leaf-mid) 0%, var(--leaf-deep) 60%, #0a2a0c 100%);
  }
  .brand-line {
    position: absolute;
    right: 22px;
    margin: 0;
    font-family: "Bebas Neue", sans-serif;
    font-weight: 400;
    color: var(--white);
    font-size: 128px;
    line-height: 1;
    letter-spacing: 1px;
    text-align: right;
    white-space: nowrap;
  }
  .brand-line--one { top: 8px; }
  .brand-line--two { top: 102px; }
  .brand-line--three { top: 196px; }
  .services {
    position: absolute;
    right: 162px;
    top: 212px;
    margin: 0;
    padding: 0;
    list-style: none;
    text-align: right;
    font-family: "Bebas Neue", sans-serif;
    color: var(--white);
    font-size: 25px;
    line-height: 24px;
    letter-spacing: 1.4px;
    white-space: nowrap;
  }
  .front-phone {
    position: absolute;
    right: 22px;
    top: 307px;
    margin: 0;
    font-family: "Bebas Neue", sans-serif;
    color: var(--phone-yellow);
    font-size: 42px;
    line-height: 1;
    letter-spacing: 1px;
  }

  /* Back */
  .orchid-photo { position: absolute; }
  .orchid-photo--magenta {
    left: 0; top: 0; width: 214px; height: 244px;
    background: radial-gradient(circle at 45% 45%, var(--orchid-magenta) 0%, #8e1470 55%, #c9d24a 100%);
  }
  .orchid-photo--yellow {
    left: 214px; top: 0; width: 214px; height: 122px;
    background: radial-gradient(circle at 50% 50%, var(--orchid-yellow) 0%, #e8a10a 50%, #2f6d86 100%);
  }
  .orchid-photo--violet {
    left: 214px; top: 122px; width: 214px; height: 122px;
    background: radial-gradient(circle at 50% 45%, #7a3cf0 0%, var(--orchid-violet) 50%, #2a7a2c 100%);
  }
  .orchid-photo--orange {
    left: 428px; top: 0; width: 216px; height: 244px;
    background: radial-gradient(circle at 50% 55%, #ff5fa0 0%, var(--orchid-orange) 45%, #2f4d24 100%);
  }
  .name-band {
    position: absolute;
    left: 0; top: 244px;
    width: 644px; height: 122px;
    background: var(--band-black);
  }
  .name-row {
    position: absolute;
    right: 22px;
    top: 14px;
    display: flex;
    align-items: flex-start;
    gap: 14px;
  }
  .specialty {
    margin: 0;
    padding-top: 4px;
    text-align: right;
    font-family: "Bebas Neue", sans-serif;
    font-size: 23px;
    line-height: 23px;
    letter-spacing: 1.2px;
    color: var(--white);
    white-space: nowrap;
  }
  .specialty .back-phone { color: var(--phone-green); display: block; }
  .owner-name {
    margin: 0;
    font-family: "Bebas Neue", sans-serif;
    font-weight: 400;
    font-size: 52px;
    line-height: 1;
    color: var(--white);
    letter-spacing: 0.5px;
    white-space: nowrap;
  }
  .credential {
    position: absolute;
    right: 22px;
    top: 86px;
    margin: 0;
    font-family: "Cabin", sans-serif;
    font-weight: 500;
    font-size: 15px;
    color: var(--white);
    letter-spacing: 0.3px;
  }
</style>
</head>
<body>
<main class="canvas">
  <section class="card card--front">
    <div class="foliage-photo" role="img" aria-label="Close-up photo of large striped tropical leaves in saturated greens"></div>
    <h1 class="brand-line brand-line--one">A Verdant</h1>
    <p class="brand-line brand-line--two">Terrace</p>
    <p class="brand-line brand-line--three">LLC</p>
    <ul class="services">
      <li>Landscape Design &amp; Build Company</li>
      <li>Landscape Lighting</li>
      <li>Drip Irrigation</li>
      <li>Ponds and Water Features</li>
    </ul>
    <p class="front-phone">T. 561-555-0147</p>
  </section>

  <section class="card card--back">
    <div class="orchid-photo orchid-photo--magenta" role="img" aria-label="Photo of magenta orchid sprays"></div>
    <div class="orchid-photo orchid-photo--yellow" role="img" aria-label="Photo of a bright yellow orchid bloom"></div>
    <div class="orchid-photo orchid-photo--violet" role="img" aria-label="Photo of violet spotted orchids"></div>
    <div class="orchid-photo orchid-photo--orange" role="img" aria-label="Photo of orange and pink orchid cluster"></div>
    <div class="name-band">
      <div class="name-row">
        <p class="specialty">Orchids and Organic Farming<span class="back-phone">T. 561-555-0147</span></p>
        <h2 class="owner-name">Corey Halvorsen</h2>
      </div>
      <p class="credential">GTA Certified Arborist NO-1234A</p>
    </div>
  </section>
</main>
</body>
</html>
```